Norrell Advisory WA Business Card

Create an interesting, eye catching and colourful two sided business card. We are a business consulting operation assisting SME's improve all areas of their business. We provide consulting services to assist SME's to create a culture of continuous improvement, making a positive difference in the business. Our tag line is Small changes, big rewards. We want to create a well recognised, innovative brand that can be continued throughout our website, social media and email correspondence.

Target Market(s)

Small to Medium Enterprise Business Owners

Industry/Entity Type

Business Consultant

Contact Information for Business Card

Name of Business: Norrell Advisory - Small Changes Big Rewards
Derek Holloway Ph 0407385510 Megan Holloway Ph 0407913847
Email norrelladvisorywa@mailbox-example.com
Web address TBA
FaceBook page TBA

BACKSIDE OF CARD

Providing assistance with:

• Organisation & Efficiency
• Revenue generation & Marketing
• Financial Management
• Production quality & delivery
• Systems & Process documentation
• Exit Strategy

Font styles to use
Other font styles liked:
• Calibri

Colors

Designer to choose colors to be used in the design.

Requirements
Must have
• Calibri font

```html
<!DOCTYPE html>
<html lang="en">
<head>
<meta charset="utf-8">
<title>Norrell Advisory WA Business Card</title>
<link href="https://fonts.googleapis.com/css2?family=Carlito:ital,wght@0,400;0,700;1,400;1,700&display=swap" rel="stylesheet">
<style>
  :root {
    --page: #e4e4e4;
    --card-white: #ffffff;
    --band-black: #1c1c1e;
    --name-blue: #0a72b5;
    --phone-grey: #d6d6d6;
    --contact-grey: #d9d9d9;
    --ink-dark: #2b2b2b;
    --ink-mid: #555555;
    --piece-red: #e8392b;
    --piece-yellow: #f7c21c;
    --piece-green: #8cc63f;
    --piece-blue: #2d9fd9;
    --divider: #5a5a5a;
  }
  * { margin: 0; padding: 0; box-sizing: border-box; }
  html, body {
    width: 1125px;
    height: 1200px;
    overflow: hidden;
    background: var(--page);
    font-family: "Carlito", "Calibri", sans-serif;
  }
  .card {
    position: absolute;
    left: 171px;
    width: 826px;
    height: 472px;
    overflow: hidden;
  }
  .card--front { top: 106px; background: var(--band-black); }
  .card--back { top: 639px; background: var(--card-white); }

  .pattern-band {
    position: absolute;
    left: 0;
    width: 100%;
    background: linear-gradient(100deg,
      var(--piece-yellow) 0%, var(--piece-red) 14%, var(--piece-green) 28%,
      var(--piece-blue) 42%, var(--piece-yellow) 56%, var(--piece-red) 70%,
      var(--piece-green) 84%, var(--piece-blue) 100%);
  }
  .pattern-band--top { top: 0; height: 126px; }
  .pattern-band--bottom { bottom: 0; height: 127px; }

  .name-block { position: absolute; top: 170px; }
  .name-block--left { right: calc(826px - 355px); text-align: right; }
  .name-block--right { left: 416px; text-align: left; }
  .person-name {
    font-weight: 700;
    font-size: 35px;
    line-height: 38px;
    color: var(--name-blue);
    white-space: nowrap;
  }
  .person-phone {
    font-weight: 700;
    font-size: 27px;
    line-height: 30px;
    color: var(--phone-grey);
    letter-spacing: 0.3px;
  }
  .name-divider {
    position: absolute;
    left: 385px;
    top: 185px;
    width: 1px;
    height: 62px;
    background: var(--divider);
  }
  .contact-line {
    position: absolute;
    top: 295px;
    left: 0;
    width: 100%;
    display: flex;
    justify-content: center;
    align-items: center;
    gap: 7px;
    font-size: 18px;
    color: var(--contact-grey);
    white-space: nowrap;
  }
  .contact-item { display: flex; align-items: center; gap: 6px; }
  .contact-icon { width: 16px; height: 16px; flex: none; }
  .contact-icon--square { background: var(--name-blue); }

  .brand-block {
    position: absolute;
    left: 0;
    width: 450px;
    top: 133px;
    text-align: center;
  }
  .brand-square {
    width: 92px;
    height: 92px;
    margin: 0 auto 26px;
    background: var(--piece-blue);
  }
  .brand-name {
    font-weight: 700;
    font-size: 32px;
    line-height: 34px;
    color: var(--ink-dark);
    letter-spacing: 0.5px;
  }
  .services {
    position: absolute;
    left: 418px;
    top: 138px;
  }
  .services-heading {
    font-weight: 700;
    font-style: italic;
    font-size: 27px;
    color: var(--ink-mid);
    margin-bottom: 6px;
  }
  .services-list { list-style: none; }
  .services-list li {
    font-size: 19px;
    line-height: 24.8px;
    color: var(--ink-mid);
    padding-left: 22px;
    position: relative;
  }
  .services-list li::before {
    content: "";
    position: absolute;
    left: 4px;
    top: 10px;
    width: 5px;
    height: 5px;
    border-radius: 50%;
    background: var(--ink-mid);
  }
</style>
</head>
<body>
  <section class="card card--front">
    <div class="pattern-band pattern-band--top" role="img" aria-label="Colourful interlocking jigsaw puzzle pattern in red, yellow, green and blue"></div>

    <div class="name-block name-block--left">
      <div class="person-name">DEREK HOLLOWAY</div>
      <div class="person-phone">0407385510</div>
    </div>
    <div class="name-divider"></div>
    <div class="name-block name-block--right">
      <div class="person-name">MEGAN HOLLOWAY</div>
      <div class="person-phone">0407913847</div>
    </div>

    <div class="contact-line">
      <span class="contact-item"><span class="contact-icon contact-icon--square"></span>norrelladvisorywa</span>
      <span class="contact-item">
        <svg class="contact-icon" viewBox="0 0 16 16"><rect x="1" y="3" width="14" height="10" fill="#2d9fd9"/><path d="M1 3 L8 9 L15 3" fill="none" stroke="#1c1c1e" stroke-width="1.4"/></svg>
        norrelladvisorywa@mailbox-example.com
      </span>
      <span class="contact-item">
        <svg class="contact-icon" viewBox="0 0 16 16"><circle cx="8" cy="8" r="7" fill="#2d9fd9"/><ellipse cx="8" cy="8" rx="3" ry="7" fill="none" stroke="#1c1c1e" stroke-width="1"/><line x1="1" y1="8" x2="15" y2="8" stroke="#1c1c1e" stroke-width="1"/></svg>
        norrelladvisorywa.example
      </span>
    </div>

    <div class="pattern-band pattern-band--bottom" role="img" aria-label="Colourful interlocking jigsaw puzzle pattern in red, yellow, green and blue"></div>
  </section>

  <section class="card card--back">
    <div class="brand-block">
      <div class="brand-square"></div>
      <div class="brand-name">NORRELL ADVISORY</div>
    </div>

    <div class="services">
      <h2 class="services-heading">Providing assistance with</h2>
      <ul class="services-list">
        <li>Organisation &amp; Efficiency</li>
        <li>Revenue generation &amp; Marketing</li>
        <li>Financial Management</li>
        <li>Production quality &amp; delivery</li>
        <li>Systems &amp; Process documentation</li>
        <li>Exit Strategy</li>
      </ul>
    </div>
  </section>
</body>
</html>
```